Sunset Harbor Living Web Page

We need a web page design that has two intro pages - first being a 'home page', then a link to the second page that has the 'content tabs' and a 'call to action' (see below).

The business helps people that wish to retire to S.E.Asia (Thailand, Malaysia, Indonesia,The Philippines etc) - to enjoy the lifestyle and the remaining years of their lives. What attracts S.E.Asia to many people is the lower cost, the atmoshpere and beauty of the tropics and the vibrancy of the various countries.

People that are wishing to make the most of their retirement and are adventurous at a great bargain compared to the cost of their own countries will be interested.

We help them achieve this - visa, financials (tax, gov't payments etc), introduce them to the right people for property, clubs, retirement facilities, insurance and so forth.

Therefore we are providing an extremely wide ranging service and this site will provide broad but general information only - with a call to action to come and see us for more specific information and how we can help them specifically.

This site will be predominantly for travel and lifestyle, it will be linked with another financial services (financial planning) site later down the track.

The colour scheme is dark green and blue - as per the attached logo design. Photos and background just think lifestyle and S.E.Asia - beaches/mountains/water/recreational activities for retirees.

Target market is mostly those coming up to retirement to those that are already retired. But we also expect to have some interest with younger people that would like to find out more and plan for the future. So a broad age group but I would say mostly 40-70 yrs old.

On the first (Home) page we would like our company name 'Sunset Harbor Living', our logo (which will be on all pages) and a statement such as: “Imagine a retirement where your dreams are brought to life, and you have never felt more alive. Let us show you how”. Then a link to the second page.

We would like an uncluttered site. On the second (contents) page the tabs would be:

- Visa
- Property
- Financials
- Travel
- Insurance & Healthcare
- Medical Tourism
- Cost of living
- Weekly Blogs and articles
- Sunset Harbor Living story

We would also like a call to action on the second page - asking them to leave their contact details if they wish to learn more or sign up to our weekly newsletter/blog.

We are open to suggestions and your imaginations.

Thank you
Malcolm

Font styles to use
Serif
Script

Colors
0255a3
3377b5
00a990
9bcb3c
abd036
33b8a4
85abd2
cadf82
86cfc6

Requirements
Must have
• I have been asked by the web designer to receive a 'Web Font' so that we can 'get off of Zentrofy'. Hope that makes sense.

```html
<!DOCTYPE html>
<html lang="en">
<head>
<meta charset="utf-8">
<title>Sunset Harbor Living</title>
<link rel="stylesheet" href="https://fonts.googleapis.com/css2?family=Open+Sans:wght@400;600;700&family=Ubuntu:wght@400;500;700&family=Ubuntu+Condensed&family=Playfair+Display:ital,wght@0,400;0,700;1,400&display=swap">
<style>
:root{
  --blue:#1c93d6;
  --blue-dark:#0f74b8;
  --blue-light:#3fa9e8;
  --green:#1fa85a;
  --green-dark:#178a49;
  --grey-card:#e9e9e9;
  --grey-band:#ececec;
  --text:#3b3b3b;
  --muted:#6d6d6d;
  --white:#ffffff;
}
*{box-sizing:border-box;margin:0;padding:0}
html,body{width:1200px;height:3689px;overflow:hidden}
body{position:relative;font-family:"Open Sans",Arial,sans-serif;color:var(--text);background:var(--white)}
.abs{position:absolute}

/* ---------- hero ---------- */
.hero{position:absolute;left:0;top:0;width:1200px;height:684px;overflow:hidden}
.hero-photo{position:absolute;inset:0;background:linear-gradient(180deg,#3b3a3c 0%,#6d5a4a 30%,#c98a4e 52%,#e6a458 58%,#6e5a4c 70%,#2d2a29 100%)}
.top-links{position:absolute;right:70px;top:12px;display:flex;gap:18px;font-size:12px;font-weight:600;color:var(--white)}
.brand{position:absolute;left:66px;top:62px;display:flex;align-items:center;gap:10px;white-space:nowrap}
.brand-dot{width:54px;height:54px;border-radius:50%;background:var(--green);flex:none}
.brand-name{font-family:"Ubuntu",Arial,sans-serif;font-weight:700;font-size:27px;color:var(--white);line-height:1;white-space:nowrap}
.contact-item{position:absolute;top:74px;display:flex;align-items:center;gap:8px;color:var(--white);font-size:13px;line-height:1.25;white-space:nowrap}
.contact-item b{font-weight:700;font-size:13px}
.round-ico{width:30px;height:30px;border-radius:50%;background:var(--green);display:flex;align-items:center;justify-content:center;flex:none}
.social{position:absolute;display:flex;gap:8px}
.social span{width:34px;height:34px;background:#8e8e8e;display:block}
.hero .social{left:930px;top:70px}
.main-nav{position:absolute;left:62px;top:160px;width:1077px;height:37px;background:var(--green);border:2px solid #5dc98a;display:flex;align-items:center;justify-content:space-between;padding:0 6px;font-family:"Ubuntu Condensed","Arial Narrow",Arial,sans-serif;font-size:12.5px;color:var(--white);text-transform:uppercase;white-space:nowrap}
.main-nav span{padding:0 5px;border-right:1px solid rgba(255,255,255,.5);line-height:1.2}
.main-nav span:last-child{border:0}
.hero-text{position:absolute;left:0;width:1200px;text-align:center;color:var(--white);font-family:"Playfair Display",Georgia,serif;white-space:nowrap}
.hero-imagine{top:318px;font-size:66px;letter-spacing:22px}
.hero-a{top:392px;font-size:34px;font-style:italic}
.hero-line{position:absolute;height:2px;background:var(--white);top:415px}
.hero-main{top:440px;font-size:50px;text-transform:uppercase}
.hero-main i{text-transform:none;font-size:46px}
.hero-sub{top:502px;font-size:30px;text-transform:uppercase}
.hero-rule{position:absolute;left:168px;top:556px;width:864px;height:2px;background:var(--white)}
.slide-arrow{position:absolute;top:430px;width:32px;height:32px;border-radius:50%;background:#1f1f1f;border:2px solid #fff;display:flex;align-items:center;justify-content:center}

/* ---------- welcome ---------- */
.welcome{position:absolute;left:0;top:684px;width:1200px;height:320px;background:var(--blue);color:var(--white);text-align:center}
.welcome h1{position:absolute;top:48px;width:100%;font-family:"Ubuntu",Arial,sans-serif;font-size:22px;font-weight:700}
.welcome .mini-dot{position:absolute;left:588px;top:82px;width:24px;height:16px;border-radius:12px 12px 0 0;background:#e7f3fb}
.welcome p{position:absolute;left:90px;top:112px;width:1020px;font-size:14px;line-height:1.65}
.btn-outline{position:absolute;left:542px;top:232px;width:116px;height:30px;border:1.5px solid var(--white);border-radius:3px;font-size:12px;display:flex;align-items:center;justify-content:center;gap:5px}

.btn{position:absolute;height:28px;background:var(--green);color:var(--white);font-size:12px;font-weight:600;border-radius:3px;display:flex;align-items:center;justify-content:center;gap:5px;text-transform:uppercase;white-space:nowrap}
.circ{display:inline-block;width:11px;height:11px;border:1.5px solid currentColor;border-radius:50%;position:relative}
.circ::after{content:"";position:absolute;left:2px;top:2.5px;width:3px;height:3px;border-top:1.5px solid currentColor;border-right:1.5px solid currentColor;transform:rotate(45deg)}

/* ---------- feature cards ---------- */
.feature{position:absolute;top:1063px;width:345px;height:393px;background:var(--grey-card);border-top:4px solid var(--green)}
.feature h3{position:absolute;left:18px;top:16px;width:220px;font-family:"Ubuntu",Arial,sans-serif;font-size:16px;font-weight:500;color:var(--blue);text-transform:uppercase;line-height:1.15}
.feature .badge{position:absolute;right:18px;top:10px;width:44px;height:44px;border-radius:50%;background:var(--green)}
.feature .photo{position:absolute;left:18px;top:70px;width:309px;height:152px}
.feature p{position:absolute;left:18px;top:237px;width:310px;font-size:13.5px;line-height:1.55;color:var(--muted)}
.feature .btn{left:18px;top:342px;width:112px}

/* ---------- property band ---------- */
.property{position:absolute;left:0;top:1506px;width:1200px;height:394px;background:var(--grey-band)}
.section-dot{position:absolute;width:56px;height:40px;border-radius:28px 28px 0 0;background:var(--green)}
.property h2{position:absolute;top:52px;width:100%;text-align:center;font-family:"Ubuntu",Arial,sans-serif;font-size:22px;font-weight:400;color:var(--blue);text-transform:uppercase}
.property .rule{position:absolute;left:304px;top:80px;width:592px;height:2px;background:var(--blue)}
.listing{position:absolute;top:100px;width:219px}
.listing .photo{width:219px;height:160px}
.listing span{display:block;margin-top:8px;font-size:13.5px;color:var(--muted)}
.carousel-arrow{position:absolute;top:178px;width:34px;height:34px;border-radius:50%;background:var(--blue);display:flex;align-items:center;justify-content:center}
.property .btn{left:526px;top:310px;width:148px}

/* ---------- lifestyle ---------- */
.lifestyle{position:absolute;left:0;top:1900px;width:1200px;height:848px}
.lifestyle h2{position:absolute;top:48px;width:100%;text-align:center;font-family:"Ubuntu",Arial,sans-serif;font-size:36px;font-weight:400;color:var(--blue);text-transform:uppercase}
.lifestyle .tagline{position:absolute;top:96px;width:100%;text-align:center;font-family:"Ubuntu",Arial,sans-serif;font-size:20px;color:var(--green);text-transform:uppercase}
.country{position:absolute;top:147px;width:335px}
.country-head{height:49px;background:var(--blue);color:var(--white);font-family:"Ubuntu",Arial,sans-serif;font-weight:500;font-size:16px;text-transform:uppercase;padding:14px 18px;white-space:nowrap}
.country .photo{height:184px}
.country h4{margin-top:20px;font-size:14px;font-weight:700;text-transform:uppercase;color:var(--text)}
.country .lead{margin-top:6px;font-size:13px;color:var(--muted);line-height:1.5;height:44px;border-bottom:1px solid #dcdcdc}
.story{display:flex;gap:14px;padding:14px 0 12px;border-bottom:1px solid #dcdcdc;height:89px}
.story .thumb{width:74px;height:64px;flex:none}
.story b{display:block;font-size:13px;color:var(--text)}
.story small{display:block;margin-top:4px;font-size:12.5px;color:var(--muted);line-height:1.4}
.scroll-track{position:absolute;left:74px;top:757px;width:1053px;height:16px;background:#d2d2d2}
.lifestyle .btn{left:544px;top:751px;width:112px}

/* ---------- bottom row ---------- */
.panel{position:absolute;top:2748px;height:401px}
.panel-title{height:52px;padding:17px 18px;font-family:"Ubuntu",Arial,sans-serif;font-weight:500;font-size:16px;color:var(--white);text-transform:uppercase;white-space:nowrap}
.panel-listen{left:74px;width:332px;background:var(--blue);box-shadow:0 3px 4px rgba(0,0,0,.25)}
.panel-listen .photo{margin:0 18px;height:210px;position:relative}
.play{position:absolute;left:120px;top:72px;width:56px;height:56px;border-radius:50%;background:var(--green);display:flex;align-items:center;justify-content:center}
.panel-listen p{padding:16px 18px;font-size:13.5px;color:var(--white);line-height:1.5}
.panel-story{left:433px;width:332px;background:var(--green);box-shadow:0 3px 4px rgba(0,0,0,.25)}
.quote-card{margin:0 18px;height:268px;background:var(--white);border-radius:3px;padding:22px 20px;position:relative}
.quote-card p{font-size:13px;font-style:italic;color:var(--muted);line-height:1.6}
.avatar{position:absolute;left:20px;top:200px;width:58px;height:58px;border-radius:50%;background:#c9b9a5}
.quote-card cite{position:absolute;left:90px;top:220px;font-style:normal;font-size:13px;font-weight:600}
.pager{position:absolute;top:355px;display:flex;gap:8px;left:126px}
.pager span{width:34px;height:34px;border:2px solid var(--white);border-radius:50%;display:flex;align-items:center;justify-content:center}
.panel-blogs{left:792px;width:335px;border:1px solid #d8d8d8;background:var(--white)}
.tabs{display:flex;height:52px;border-bottom:1px solid #d8d8d8}
.tabs span{flex:1;display:flex;align-items:center;justify-content:center;font-family:"Ubuntu",Arial,sans-serif;font-size:16px;text-transform:uppercase}
.tabs span:first-child{color:var(--blue);border-right:1px solid #d8d8d8}
.tabs span:last-child{background:#f3f3f3;color:var(--text)}
.blog{display:flex;gap:14px;padding:16px 18px 8px}
.blog .thumb{width:60px;height:58px;flex:none;border-radius:3px}
.blog b{display:block;font-size:13px}
.blog small{display:block;font-size:12px;color:var(--muted);line-height:1.4;margin-top:3px}
.panel-blogs .btn{left:18px;top:355px;width:112px}

/* ---------- footer ---------- */
.footer{position:absolute;left:0;top:3160px;width:1200px;height:529px}
.footer-wave{position:absolute;left:0;top:0}
.footer-body{position:absolute;left:0;top:80px;width:1200px;height:420px;background:var(--blue-dark);color:var(--white)}
.footer-col{position:absolute;font-size:13px;line-height:1.9;white-space:nowrap}
.footer-col h5{font-family:"Ubuntu",Arial,sans-serif;font-weight:500;font-size:13px;text-transform:uppercase;margin-bottom:10px;line-height:1}
.footer-col.newsletter{white-space:normal;width:290px;line-height:1.6}
.footer-col input{display:block;width:274px;height:30px;border:0;margin-top:10px;padding:0 10px;font-size:12px;color:#888}
.subscribe{display:inline-block;margin-top:12px;background:var(--blue-light);padding:4px 12px;font-size:12px;font-weight:700;line-height:1.6}
.footer-social{left:885px;top:96px}
.footer-social span{background:var(--blue-light)}
.footer-contact{position:absolute;left:74px;top:280px;display:flex;gap:40px;font-size:14px;align-items:center;white-space:nowrap}
.footer-contact div{display:flex;gap:8px;align-items:center}
.ring{width:30px;height:30px;border:1.5px solid var(--white);border-radius:50%;display:flex;align-items:center;justify-content:center}
.footer-brand{position:absolute;left:860px;top:170px;display:flex;flex-direction:column;align-items:center;gap:12px;width:300px}
.footer-brand .brand-dot{width:80px;height:80px;background:var(--white)}
.footer-brand .brand-name{font-size:24px;text-align:center}
.legal{position:absolute;left:0;bottom:0;width:1200px;height:29px;background:var(--green);color:var(--white);font-size:12px;text-align:center;line-height:29px}
</style>
</head>
<body>

<header class="hero">
  <div class="hero-photo" role="img" aria-label="Tropical beach at sunset with a thatched umbrella and sun loungers"></div>
  <nav class="top-links"><span>HOME</span><span>ABOUT US</span><span>CONTACT US</span></nav>
  <div class="brand"><span class="brand-dot"></span><span class="brand-name">Sunset Harbor Living</span></div>
  <div class="contact-item" style="left:450px">
    <span class="round-ico"><svg width="14" height="14" viewBox="0 0 24 24"><path fill="#fff" d="M6.6 10.8a15 15 0 0 0 6.6 6.6l2.2-2.2c.3-.3.7-.4 1-.2 1.1.4 2.3.6 3.6.6.6 0 1 .4 1 1V20c0 .6-.4 1-1 1A17 17 0 0 1 3 4c0-.6.4-1 1-1h3.5c.6 0 1 .4 1 1 0 1.3.2 2.5.6 3.6.1.3 0 .7-.2 1z"/></svg></span>
    <div>Call Us:<br><b>+1-000-000-0000</b></div>
  </div>
  <div class="contact-item" style="left:640px">
    <span class="round-ico"><svg width="14" height="12" viewBox="0 0 24 18"><rect x="1" y="1" width="22" height="16" fill="none" stroke="#fff" stroke-width="2"/><path d="M1 1l11 9 11-9" fill="none" stroke="#fff" stroke-width="2"/></svg></span>
    <div>Email Us:<br><b>info@sunsetharborliving.com</b></div>
  </div>
  <div class="social"><span></span><span></span><span></span><span></span><span></span></div>
  <nav class="main-nav">
    <span>Visa</span><span>Property</span><span>Financials</span><span>Travel</span><span>Insurance &amp; Healthcare</span><span>Medical Tourism</span><span>Cost of Living</span><span>Weekly Blogs &amp; Articles</span><span>Sunset Harbor Living Story</span>
  </nav>
  <div class="hero-text hero-imagine">IMAGINE</div>
  <div class="hero-line" style="left:330px;width:225px"></div>
  <div class="hero-line" style="left:645px;width:225px"></div>
  <div class="hero-text hero-a">a</div>
  <div class="hero-text hero-main">Retirement where <i>your</i> dreams</div>
  <div class="hero-text hero-sub">Are brought to life, and you have never felt more alive.</div>
  <div class="hero-rule"></div>
  <div class="slide-arrow" style="left:40px"><svg width="12" height="12" viewBox="0 0 12 12"><path d="M8 2L4 6l4 4" stroke="#fff" stroke-width="2" fill="none"/></svg></div>
  <div class="slide-arrow" style="left:1126px"><svg width="12" height="12" viewBox="0 0 12 12"><path d="M4 2l4 4-4 4" stroke="#fff" stroke-width="2" fill="none"/></svg></div>
</header>

<section class="welcome">
  <h1>WELCOME TO SUNSET HARBOR LIVING</h1>
  <span class="mini-dot"></span>
  <p>Lorem ipsum dolor sit amet, consectetur adipiscing elit, sed do eiusmod tempor incididunt ut labore et dolore magna aliqua. Ut enim ad minim veniam, quis nostrud exercitation ullamco laboris nisi ut aliquip ex ea commodo consequat. Duis aute irure dolor in reprehenderit in voluptate velit esse cillum dolore eu fugiat nulla pariatur. Excepteur sint occaecat cupidatat non proident, sunt in culpa qui officia deserunt mollit anim id est laborum.</p>
  <div class="btn-outline">READ MORE <span class="circ"></span></div>
</section>

<section>
  <article class="feature" style="left:74px">
    <h3>What about your financial future?</h3><span class="badge"></span>
    <div class="photo" role="img" aria-label="Hands working on a laptop with financial charts" style="background:linear-gradient(135deg,#1d3f66,#3d7fb8 55%,#a9c8e6)"></div>
    <p>Lorem ipsum dolor sit amet, consectetur adipiscing elit, sed do eiusmod tempor incididunt ut labore et dolore magna aliqua. Ut enim ad</p>
    <div class="btn">Read more <span class="circ"></span></div>
  </article>
  <article class="feature" style="left:433px">
    <h3>Insurance &amp;<br>Healthcare</h3><span class="badge"></span>
    <div class="photo" role="img" aria-label="Medical insurance form with a stethoscope" style="background:linear-gradient(135deg,#dfe9f2,#9cbfd9 60%,#5e8fb6)"></div>
    <p>Lorem ipsum dolor sit amet, consectetur adipiscing elit, sed do eiusmod tempor incididunt ut labore et dolore magna aliqua. Ut enim ad</p>
    <div class="btn">Read more <span class="circ"></span></div>
  </article>
  <article class="feature" style="left:792px">
    <h3>Medical<br>Tourism</h3><span class="badge"></span>
    <div class="photo" role="img" aria-label="World map with a stethoscope laid across it" style="background:linear-gradient(135deg,#e4d7b4,#c9b98d 45%,#d8573c 75%,#6ea3c4)"></div>
    <p>Lorem ipsum dolor sit amet, consectetur adipiscing elit, sed do eiusmod tempor incididunt ut labore et dolore magna aliqua. Ut enim ad</p>
    <div class="btn">Read more <span class="circ"></span></div>
  </article>
</section>

<section class="property">
  <span class="section-dot" style="left:572px;top:10px"></span>
  <h2>List a property!</h2>
  <div class="rule"></div>
  <div class="carousel-arrow" style="left:74px"><svg width="12" height="12" viewBox="0 0 12 12"><path d="M8 2L4 6l4 4" stroke="#fff" stroke-width="2" fill="none"/></svg></div>
  <div class="listing" style="left:133px"><div class="photo" role="img" aria-label="Thai style wooden house" style="background:linear-gradient(180deg,#6aa8e0,#b8752e 55%,#5a8a3a)"></div><span>Lorem House for Sale</span></div>
  <div class="listing" style="left:371px"><div class="photo" role="img" aria-label="Traditional temple style villa" style="background:linear-gradient(180deg,#8fc0ea,#7a5a3a 55%,#4f7e3a)"></div><span>Lorem House for Sale</span></div>
  <div class="listing" style="left:610px"><div class="photo" role="img" aria-label="Tropical house among palm trees" style="background:linear-gradient(180deg,#9ccbef,#a0522d 50%,#3f7a34)"></div><span>Lorem House for Sale</span></div>
  <div class="listing" style="left:849px"><div class="photo" role="img" aria-label="Thai style wooden house" style="background:linear-gradient(180deg,#6aa8e0,#b8752e 55%,#5a8a3a)"></div><span>Lorem House for Sale</span></div>
  <div class="carousel-arrow" style="left:1090px"><svg width="12" height="12" viewBox="0 0 12 12"><path d="M4 2l4 4-4 4" stroke="#fff" stroke-width="2" fill="none"/></svg></div>
  <div class="btn">List a property! <span class="circ"></span></div>
</section>

<section class="lifestyle">
  <span class="section-dot" style="left:268px;top:50px;width:60px;height:30px"></span>
  <span class="section-dot" style="left:872px;top:50px;width:60px;height:30px"></span>
  <h2>Enjoy the lifestyle and</h2>
  <p class="tagline">The remaining years of their lives</p>

  <div class="country" style="left:74px">
    <div class="country-head">Retire to Thailand</div>
    <div class="photo" role="img" aria-label="Limestone island and longtail boat on turquoise water" style="background:linear-gradient(180deg,#8cc5ea,#5d8a5a 45%,#2fb3b6 75%,#e6dcc0)"></div>
    <h4>Lifestyle in Thailand</h4>
    <p class="lead">Lorem ipsum dolor sit amet, consectetur adipiscing elit</p>
    <div class="story"><div class="thumb" role="img" aria-label="Forest path" style="background:linear-gradient(135deg,#6c8d4a,#c8b47a)"></div><div><b>Lorem ipsum dolor sit amet</b><small>Sed ut perspiciatis unde omnis iste natus error sit voluptatem.</small></div></div>
    <div class="story"><div class="thumb" role="img" aria-label="Beach at dusk" style="background:linear-gradient(180deg,#d7a16a,#5a7f9e)"></div><div><b>Lorem ipsum dolor sit amet</b><small>Sed ut perspiciatis unde omnis iste natus error sit voluptatem.</small></div></div>
    <div class="story"><div class="thumb" role="img" aria-label="Rock island in the sea" style="background:linear-gradient(180deg,#7fb7e0,#4d6a44 55%,#2fa7b3)"></div><div><b>Lorem ipsum dolor sit amet</b><small>Sed ut perspiciatis unde omnis iste natus error sit voluptatem.</small></div></div>
  </div>

  <div class="country" style="left:433px">
    <div class="country-head">Retire to Malaysia</div>
    <div class="photo" role="img" aria-label="Red lantern decorated temple roof at night" style="background:linear-gradient(180deg,#1d3f7a,#c2332a 55%,#e79a3a)"></div>
    <h4>Lifestyle in Malaysia</h4>
    <p class="lead">Lorem ipsum dolor sit amet, consectetur adipiscing elit</p>
    <div class="story"><div class="thumb" role="img" aria-label="Beach with boats" style="background:linear-gradient(180deg,#8cc5ea,#32b0b8 60%,#e3d6b4)"></div><div><b>Lorem ipsum dolor sit amet</b><small>Sed ut perspiciatis unde omnis iste natus error sit voluptatem.</small></div></div>
    <div class="story"><div class="thumb" role="img" aria-label="Beach with boats" style="background:linear-gradient(180deg,#8cc5ea,#32b0b8 60%,#e3d6b4)"></div><div><b>Lorem ipsum dolor sit amet</b><small>Sed ut perspiciatis unde omnis iste natus error sit voluptatem.</small></div></div>
    <div class="story"><div class="thumb" role="img" aria-label="Beach with boats" style="background:linear-gradient(180deg,#8cc5ea,#32b0b8 60%,#e3d6b4)"></div><div><b>Lorem ipsum dolor sit amet</b><small>Sed ut perspiciatis unde omnis iste natus error sit voluptatem.</small></div></div>
  </div>

  <div class="country" style="left:792px">
    <div class="country-head">Retire to the Philippines</div>
    <div class="photo" role="img" aria-label="Green lagoon surrounded by cliffs" style="background:linear-gradient(180deg,#9cc7e8,#3e6f3e 45%,#2e9a8a 80%)"></div>
    <h4>Lifestyle in the Philippines</h4>
    <p class="lead">Lorem ipsum dolor sit amet, consectetur adipiscing elit</p>
    <div class="story"><div class="thumb" role="img" aria-label="Beach with boats" style="background:linear-gradient(180deg,#8cc5ea,#32b0b8 60%,#e3d6b4)"></div><div><b>Lorem ipsum dolor sit amet</b><small>Sed ut perspiciatis unde omnis iste natus error sit voluptatem.</small></div></div>
    <div class="story"><div class="thumb" role="img" aria-label="Beach with boats" style="background:linear-gradient(180deg,#8cc5ea,#32b0b8 60%,#e3d6b4)"></div><div><b>Lorem ipsum dolor sit amet</b><small>Sed ut perspiciatis unde omnis iste natus error sit voluptatem.</small></div></div>
    <div class="story"><div class="thumb" role="img" aria-label="Beach with boats" style="background:linear-gradient(180deg,#8cc5ea,#32b0b8 60%,#e3d6b4)"></div><div><b>Lorem ipsum dolor sit amet</b><small>Sed ut perspiciatis unde omnis iste natus error sit voluptatem.</small></div></div>
  </div>

  <div class="scroll-track"></div>
  <div class="btn">View more <span class="circ"></span></div>
</section>

<section>
  <div class="panel panel-listen">
    <div class="panel-title">Listen to what this site is about</div>
    <div class="photo" role="img" aria-label="Video still of the company founder speaking" style="background:linear-gradient(135deg,#2b2b2b,#6a5446 55%,#8a7a66)">
      <span class="play"><svg width="20" height="22" viewBox="0 0 20 22"><path d="M3 2l15 9-15 9z" fill="#fff"/></svg></span>
    </div>
    <p>Lorem ipsum dolor sit amet, consectetur adipiscing elit, sed do eiusmod tempor incididunt ut labore et dolore magna aliqua. Ut enim ad</p>
  </div>

  <div class="panel panel-story">
    <div class="panel-title">Sunset Harbor Living story</div>
    <div class="quote-card">
      <p>"Lorem ipsum dolor sit amet, consectetur adipiscing elit, sed do eiusmod tempor incididunt ut labore et dolore magna aliqua. Ut enim ad minim veniam, quis nostrud exercitation ullamco laboris nisi ut aliquip ex ea commodo"</p>
      <span class="avatar" role="img" aria-label="Portrait of the client"></span>
      <cite>-John Doe</cite>
    </div>
    <div class="pager">
      <span><svg width="12" height="12" viewBox="0 0 12 12"><path d="M8 2L4 6l4 4" stroke="#fff" stroke-width="2" fill="none"/></svg></span>
      <span><svg width="12" height="12" viewBox="0 0 12 12"><path d="M4 2l4 4-4 4" stroke="#fff" stroke-width="2" fill="none"/></svg></span>
    </div>
  </div>

  <div class="panel panel-blogs">
    <div class="tabs"><span>Weekly blogs</span><span>Articles</span></div>
    <div class="blog"><div class="thumb" role="img" aria-label="Retired couple outdoors" style="background:linear-gradient(135deg,#c9b08e,#8fb4cf)"></div><div><b>Lorem ipsum dolor sit amet</b><small>July 2, 2015. No Comments on Ut enim ad minim veniam.</small></div></div>
    <div class="blog"><div class="thumb" role="img" aria-label="Retired couple smiling" style="background:linear-gradient(135deg,#b8a288,#d9d0c0)"></div><div><b>Lorem ipsum dolor sit amet</b><small>July 2, 2015. No Comments on Ut enim ad minim veniam.</small></div></div>
    <div class="blog"><div class="thumb" role="img" aria-label="Retired couple on a walk" style="background:linear-gradient(135deg,#a99480,#c7d6c0)"></div><div><b>Lorem ipsum dolor sit amet</b><small>July 2, 2015. No Comments on Ut enim ad minim veniam.</small></div></div>
    <div class="btn">Read more <span class="circ"></span></div>
  </div>
</section>

<footer class="footer">
  <svg class="footer-wave" width="1200" height="100" viewBox="0 0 1200 100" preserveAspectRatio="none">
    <path d="M0 40 C80 20 140 55 220 38 C300 22 360 58 450 42 C520 30 540 60 600 55 C660 50 700 28 780 40 C860 52 920 22 1000 36 C1080 50 1140 30 1200 42 V100 H0Z" fill="#0f74b8"/>
  </svg>
  <svg class="abs" style="left:530px;top:0" width="140" height="84" viewBox="0 0 140 84"><path d="M2 84 A68 68 0 0 1 138 84Z" fill="#1fa85a"/></svg>
  <div class="footer-body">
    <div class="footer-col" style="left:74px;top:50px"><h5>Quick links</h5>Visa<br>Property<br>Financials<br>Travel<br>Insurance &amp; Healthcare</div>
    <div class="footer-col" style="left:229px;top:73px">Medical Tourism<br>Cost of living<br>Weekly Blogs &amp; articles<br>Sunset Harbor Living story</div>
    <div class="footer-col" style="left:406px;top:50px"><h5>More links</h5>Careers<br>Privacy Policy<br>Terms And Conditions<br>Traveler Resources</div>
    <div class="footer-col newsletter" style="left:573px;top:50px"><h5>Subscribe to our newsletter</h5>Keep up to date with our new hire products and special offers<input type="text" value="Enter your email address" aria-label="Email address"><span class="subscribe">SUBSCRIBE</span></div>
    <div class="footer-col" style="left:885px;top:50px"><h5>Follow us</h5></div>
    <div class="social footer-social"><span></span><span></span><span></span><span></span><span></span></div>
    <div class="footer-col" style="left:74px;top:253px"><h5>Contact us</h5></div>
    <div class="footer-contact">
      <div><span class="ring"><svg width="14" height="14" viewBox="0 0 24 24"><path fill="#fff" d="M6.6 10.8a15 15 0 0 0 6.6 6.6l2.2-2.2c.3-.3.7-.4 1-.2 1.1.4 2.3.6 3.6.6.6 0 1 .4 1 1V20c0 .6-.4 1-1 1A17 17 0 0 1 3 4c0-.6.4-1 1-1h3.5c.6 0 1 .4 1 1 0 1.3.2 2.5.6 3.6.1.3 0 .7-.2 1z"/></svg></span>+1-000-000-0000</div>
      <div><span class="ring"><svg width="14" height="11" viewBox="0 0 24 18"><rect x="1" y="1" width="22" height="16" fill="none" stroke="#fff" stroke-width="2"/><path d="M1 1l11 9 11-9" fill="none" stroke="#fff" stroke-width="2"/></svg></span>info@sunsetharborliving.com</div>
    </div>
    <div class="footer-brand"><span class="brand-dot"></span><span class="brand-name">Sunset Harbor Living</span></div>
  </div>
  <div class="legal">© 2016 Sunset Harbor Living. All Rights Reserved</div>
</footer>

</body>
</html>
```